Coastline Premier Retreats Business Card Design

Design a business card for Coastline Premier Retreats. Look at the website for colors and reference. Card should have logo, name, title, office number, mobile number, email, URL and a tagline like, "Luxury Hotel & Resort Email Marketing" (This might change).

https://www.coastlinepremierretreats.example

The rest I will leave up to your imagination.

Contact Information for Business Card

Logo, name, title, office number, mobile number, email, URL and a tagline like, "Luxury Hotel & Resort Email Marketing" (This might change).

```html
<!DOCTYPE html>
<html lang="en">
<head>
<meta charset="utf-8">
<title>Coastline Premier Retreats – Business Card</title>
<link href="https://fonts.googleapis.com/css2?family=Roboto:wght@400;700&display=swap" rel="stylesheet">
<style>
  :root {
    --ink: #111111;
    --paper: #fbfbfb;
    --night: #050505;
    --accent: #f07a10;
    --muted: #6b6b6b;
    --stage: #e7e5e2;
  }
  * { margin: 0; padding: 0; box-sizing: border-box; }
  html, body { width: 1200px; height: 960px; overflow: hidden; }
  body {
    background: var(--stage);
    font-family: "Roboto", Arial, sans-serif;
    display: flex; flex-direction: column; align-items: center; justify-content: center;
    gap: 48px;
  }
  .card {
    position: relative;
    width: 620px; height: 354px;
    border-radius: 18px;
    box-shadow: 0 10px 30px rgba(0,0,0,.18);
    overflow: hidden;
  }
  /* Back side */
  .card-back { background: var(--night); }
  .card-back .wordmark {
    position: absolute; left: 0; right: 0; top: 128px;
    text-align: center; color: #ffffff;
    font-weight: 700; font-size: 34px; letter-spacing: 3px; text-transform: uppercase;
  }
  .card-back .site {
    position: absolute; left: 0; right: 0; top: 232px;
    text-align: center; color: var(--accent);
    font-size: 15px; letter-spacing: 3px;
  }
  /* Front side */
  .card-front { background: var(--paper); color: var(--ink); }
  .card-front .wordmark {
    position: absolute; left: 0; right: 0; top: 40px;
    text-align: center; color: var(--ink);
    font-weight: 700; font-size: 22px; letter-spacing: 2px; text-transform: uppercase;
  }
  .person { position: absolute; left: 0; right: 0; top: 96px; text-align: center; }
  .person .name { font-weight: 700; font-size: 24px; }
  .person .title { font-size: 15px; color: var(--muted); margin-top: 2px; }
  .frame { position: absolute; left: 0; top: 0; }
  .contact { position: absolute; font-size: 15px; display: flex; align-items: center; gap: 6px; white-space: nowrap; }
  .contact svg { flex: none; }
  .email { left: 56px; top: 176px; }
  .phones { left: 170px; top: 206px; gap: 18px; }
  .phones span { display: flex; align-items: center; gap: 6px; }
  .web { left: 250px; top: 236px; }
  .tagline { position: absolute; left: 0; right: 0; top: 272px; text-align: center; font-size: 16px; }
</style>
</head>
<body>

  <section class="card card-back" aria-label="Card back">
    <div class="wordmark">Coastline Premier Retreats</div>
    <div class="site">coastlinepremierretreats.example</div>
  </section>

  <section class="card card-front" aria-label="Card front">
    <div class="wordmark">Coastline Premier Retreats</div>

    <div class="person">
      <div class="name">Daniel Reeve</div>
      <div class="title">President</div>
    </div>

    <svg class="frame" width="620" height="354" viewBox="0 0 620 354" aria-hidden="true">
      <polyline points="120,222 44,222 44,156 576,156 576,306 500,306"
                fill="none" stroke="var(--accent)" stroke-width="6"/>
    </svg>

    <div class="contact email">
      <svg width="14" height="10" viewBox="0 0 14 10"><rect width="14" height="10" fill="var(--accent)"/><polyline points="0,0 7,6 14,0" fill="none" stroke="#fff" stroke-width="1.3"/></svg>
      info@coastlinepremierretreats.example
    </div>

    <div class="contact phones">
      <span>
        <svg width="12" height="14" viewBox="0 0 12 14"><path d="M2 1 L5 1 L6 4 L4 5 Q5 8 8 10 L9 8 L12 9 L12 12 Q11 14 8 13 Q2 10 1 4 Q1 1 2 1Z" fill="var(--accent)"/></svg>
        555.014.6000
      </span>
      <span>
        <svg width="10" height="16" viewBox="0 0 10 16"><rect x="1" y="1" width="8" height="14" rx="1.5" fill="none" stroke="var(--accent)" stroke-width="1.6"/><circle cx="5" cy="12.5" r="0.9" fill="var(--accent)"/></svg>
        555.014.6001
      </span>
    </div>

    <div class="contact web">
      <svg width="14" height="14" viewBox="0 0 14 14"><circle cx="7" cy="7" r="7" fill="var(--accent)"/></svg>
      www.coastlinepremierretreats.example
    </div>

    <div class="tagline">Luxury Hotel &amp; Resort Email Marketing</div>
  </section>

</body>
</html>
```